SOLVE Study flyer

I need help designing a flyer for a research study that will include brain imaging in adolescents. The info is in the attached document. The study is called the Sequoia Outlook Lantern Valley Echo (SOLVE) study. Ideally this would be returned as a document that I can edit in the future as we will have several new recruitment phases (different age groups, etc. I also would love to have a logo designed as part of this project, but I recognize that might be a separate design request.

```html
<!DOCTYPE html>
<html lang="en">
<head>
<meta charset="utf-8">
<title>SOLVE Study Flyer</title>
<link rel="stylesheet" href="https://fonts.googleapis.com/css2?family=Bebas+Neue&family=Manrope:wght@400;500;600;700&family=Montserrat:wght@500;600&display=swap">
<style>
:root{
  --bg:#0a0f2e;
  --bg-deep:#070b24;
  --panel:#111a42;
  --panel-line:#26305e;
  --white:#ffffff;
  --text-soft:#d8dcf0;
  --purple:#a47fe2;
  --teal:#4fd1c5;
  --teal-soft:#5fcfc6;
}
*{margin:0;padding:0;box-sizing:border-box}
html,body{width:800px;height:1200px;overflow:hidden;background:var(--bg)}
body{font-family:"Manrope",sans-serif;color:var(--white)}
.flyer{position:relative;width:800px;height:1200px;background:linear-gradient(180deg,var(--bg-deep),var(--bg) 60%,#0b1132);overflow:hidden}
.abs{position:absolute}

.hero-photo{left:328px;top:0;width:472px;height:594px;
  background:radial-gradient(ellipse at 58% 38%,#6b4a44 0%,#3a2a3a 22%,#1d2352 48%,transparent 75%),
  radial-gradient(ellipse at 88% 22%,#4c5a8c 0%,#202a5c 35%,transparent 65%),
  linear-gradient(90deg,var(--bg-deep),#141c4a 40%,#10173e)}
.rings{left:0;top:0;width:800px;height:1200px;pointer-events:none}

.brand{left:30px;top:30px;display:flex;align-items:flex-start;gap:14px}
.brand-dot{width:62px;height:62px;border-radius:50%;border:2px solid var(--teal);margin-top:2px}
.brand-name{font-family:"Montserrat",sans-serif;font-weight:500;font-size:38px;letter-spacing:6px;line-height:42px}
.brand-sub{font-family:"Montserrat",sans-serif;font-weight:500;font-size:9.6px;letter-spacing:.8px;line-height:15px;margin-top:10px}
.brand-sub .accent{color:var(--purple)}

.headline{left:33px;top:127px;font-family:"Bebas Neue",sans-serif;font-weight:400;font-size:118px;line-height:91px;transform:scaleY(1.27);transform-origin:top left;letter-spacing:-1px}
.headline span{display:block}
.headline .mind{color:var(--purple)}

.tagline{left:180px;top:247px;font-size:15px;line-height:19.5px;color:var(--teal-soft)}
.tagline-rule{left:180px;top:345px;width:38px;height:2px;background:var(--teal)}

.comp{left:622px;top:474px;width:146px;height:146px;border-radius:50%;border:1.5px solid var(--teal);text-align:center;background:rgba(10,15,46,.55)}
.comp-label{font-family:"Montserrat",sans-serif;font-size:12.5px;letter-spacing:.5px;line-height:20px;margin-top:30px}
.comp-amount{font-size:38px;font-weight:700;color:var(--purple);line-height:44px}

.parent-band{left:29px;top:595px;width:742px;height:96px;background:rgba(17,26,66,.85)}
.parent-icon{left:46px;top:612px}
.parent-q{left:139px;top:610px;font-size:22px;font-weight:500;line-height:31px}
.parent-q strong{color:var(--purple);font-weight:600}
.band-divider{width:1px;background:var(--panel-line)}
.parent-worry{left:453px;top:608px;font-size:16.5px;line-height:23px}

.section-head{font-size:12.3px;letter-spacing:.6px;color:var(--teal);font-weight:500;line-height:20px}
.steps-head{left:38px;top:711px}
.step{left:36px;display:flex;gap:19px;align-items:flex-start}
.step-icon{width:64px;height:64px;flex:none}
.step-text{font-size:11.6px;line-height:16.5px;color:var(--text-soft)}
.step-text b{display:block;font-weight:500;font-size:12.8px;color:var(--white);letter-spacing:.3px;line-height:19px}

.elig-head{left:355px;top:716px;font-size:13.6px;line-height:21px;letter-spacing:.6px}
.elig-item{left:354px;display:flex;gap:10px;font-size:15px;line-height:20.5px}
.elig-item svg{flex:none;margin-top:0}

.mri{left:559px;top:700px;width:225px;height:312px;
  background:radial-gradient(ellipse 45% 48% at 50% 50%,#6a7cb4 0%,#34447e 55%,#141c48 80%,transparent 95%),var(--bg)}

.contact-band{left:29px;top:1025px;width:742px;height:84px;background:var(--panel)}
.contact-ask{left:125px;top:1036px;font-size:16.5px;letter-spacing:.6px;line-height:22px}
.contact-ask .accent{color:var(--purple)}
.contact-ask small{display:block;font-size:12.3px;letter-spacing:0;line-height:20px}
.contact-email{left:455px;top:1042px;font-size:23px;font-weight:500}
.contact-rule{left:455px;top:1081px;width:43px;height:3px;background:var(--teal)}

.uni{left:51px;top:1140px;display:flex;align-items:center;gap:10px}
.uni-mark{width:34px;height:34px;background:var(--white)}
.uni-name{font-size:22px;font-weight:500;line-height:26px}
.footer-note{font-size:10.4px;line-height:15.5px;color:var(--text-soft)}
</style>
</head>
<body>
<main class="flyer">
  <div class="abs hero-photo" role="img" aria-label="Portrait of a teenage girl in a hoodie looking upward, beside a sagittal brain scan"></div>

  <svg class="abs rings" viewBox="0 0 800 1200" aria-hidden="true">
    <circle cx="770" cy="470" r="200" fill="none" stroke="#4fd1c5" stroke-opacity=".45" stroke-width="1"/>
    <circle cx="700" cy="90" r="190" fill="none" stroke="#4fd1c5" stroke-opacity=".25" stroke-width="1"/>
  </svg>

  <header class="abs brand">
    <div class="brand-dot"></div>
    <div>
      <div class="brand-name">SOLVE</div>
      <div class="brand-sub">SEQUOIA OUTLOOK LANTERN<br><span class="accent">VALLEY ECHO STUDY</span></div>
    </div>
  </header>

  <h1 class="abs headline"><span>INSIDE</span><span>THE</span><span>DEVELOPING</span><span class="mind">MIND.</span></h1>

  <p class="abs tagline">Exploring how<br>emotions, decisions,<br>and puberty shape<br>adolescent brain<br>development.</p>
  <div class="abs tagline-rule"></div>

  <div class="abs comp">
    <div class="comp-label">COMPENSATION<br>UP TO</div>
    <div class="comp-amount">$140</div>
  </div>

  <section class="abs parent-band"></section>
  <svg class="abs parent-icon" width="56" height="60" viewBox="0 0 56 60" fill="none" stroke="#4fd1c5" stroke-width="1.8" aria-hidden="true">
    <circle cx="20" cy="12" r="10"/>
    <path d="M2 50v-8a16 16 0 0 1 26-12"/>
    <circle cx="37" cy="30" r="8"/>
    <path d="M24 58v-5a13 13 0 0 1 26 0v5"/>
    <rect x="12" y="46" width="6" height="5" rx="1" stroke="#a47fe2"/>
  </svg>
  <p class="abs parent-q">Are you the parent of a<br><strong>child age 10–17?</strong></p>
  <div class="abs band-divider" style="left:428px;top:615px;height:58px"></div>
  <p class="abs parent-worry">Do they worry or<br>overthink negative<br>emotions?</p>

  <h2 class="abs section-head steps-head">STUDY PARTICIPATION INVOLVES:</h2>

  <div class="abs step" style="top:741px">
    <svg class="step-icon" viewBox="0 0 64 64" fill="none" stroke="#a47fe2" stroke-width="1.6" aria-hidden="true"><circle cx="32" cy="32" r="31"/><path d="M20 22h24a3 3 0 0 1 3 3v13a3 3 0 0 1-3 3H30l-7 6v-6h-3a3 3 0 0 1-3-3V25a3 3 0 0 1 3-3z"/><circle cx="26" cy="31.5" r="1.4" fill="#a47fe2"/><circle cx="32" cy="31.5" r="1.4" fill="#a47fe2"/><circle cx="38" cy="31.5" r="1.4" fill="#a47fe2"/></svg>
    <p class="step-text"><b>ONE ONE-HOUR INTERVIEW</b>(online or in-person)<br>where your child will<br>discuss their thoughts</p>
  </div>
  <div class="abs step" style="top:827px">
    <svg class="step-icon" viewBox="0 0 64 64" fill="none" stroke="#4fd1c5" stroke-width="1.6" aria-hidden="true"><circle cx="32" cy="32" r="31"/><rect x="21" y="18" width="22" height="29" rx="2"/><rect x="27" y="15" width="10" height="5" rx="1"/><path d="M25 27l2 2 3-3M32 28h7M25 34l2 2 3-3M32 35h7M25 41l2 2 3-3M32 42h7"/></svg>
    <p class="step-text" style="padding-top:12px"><b>ONLINE QUESTIONNAIRES</b>(parent and child)</p>
  </div>
  <div class="abs step" style="top:906px">
    <svg class="step-icon" viewBox="0 0 64 64" fill="none" stroke="#a47fe2" stroke-width="1.6" aria-hidden="true"><circle cx="32" cy="32" r="31"/><path d="M18 44V30a14 14 0 0 1 28 0v14z"/><circle cx="32" cy="32" r="7"/><path d="M15 44h34"/></svg>
    <p class="step-text"><b>ONE TWO-HOUR VISIT</b>where your child will complete<br>an MRI scan, answer questions<br>about their puberty stage, and<br>have a small hair sample taken<br>to study puberty hormones</p>
  </div>

  <div class="abs band-divider" style="left:330px;top:708px;height:300px"></div>

  <h2 class="abs section-head elig-head">YOUR CHILD MAY BE<br>ELIGIBLE IF THEY:</h2>
  <div class="abs elig-item" style="top:778px">
    <svg width="22" height="22" viewBox="0 0 22 22" fill="none" stroke="#4fd1c5" stroke-width="1.6" aria-hidden="true"><circle cx="11" cy="11" r="10"/><path d="M6.5 11.5l3 3 6-6.5"/></svg>
    <span>Are age 10–17</span>
  </div>
  <div class="abs elig-item" style="top:828px">
    <svg width="22" height="22" viewBox="0 0 22 22" fill="none" stroke="#4fd1c5" stroke-width="1.6" aria-hidden="true"><circle cx="11" cy="11" r="10"/><path d="M6.5 11.5l3 3 6-6.5"/></svg>
    <span>Tend to worry or<br>overthink negative<br>thoughts</span>
  </div>
  <div class="abs elig-item" style="top:911px">
    <svg width="22" height="22" viewBox="0 0 22 22" fill="none" stroke="#4fd1c5" stroke-width="1.6" aria-hidden="true"><circle cx="11" cy="11" r="10"/><path d="M6.5 11.5l3 3 6-6.5"/></svg>
    <span>Have not been<br>diagnosed with<br>psychosis, learning<br>problems, or autism</span>
  </div>

  <div class="abs band-divider" style="left:555px;top:708px;height:300px"></div>

  <div class="abs mri" role="img" aria-label="Axial MRI brain scan with teal crosshair guide lines"></div>

  <section class="abs contact-band"></section>
  <svg class="abs" style="left:48px;top:1036px" width="60" height="60" viewBox="0 0 60 60" fill="none" stroke="#a47fe2" stroke-width="1.6" aria-hidden="true"><circle cx="30" cy="30" r="29"/><rect x="17" y="21" width="26" height="18" rx="1.5"/><path d="M17 22l13 10 13-10M17 39l9-8M43 39l-9-8"/></svg>
  <p class="abs contact-ask">INTERESTED IN PARTICIPATING?<br><span class="accent">WANT MORE INFORMATION?</span><small>Please contact us!</small></p>
  <div class="abs band-divider" style="left:423px;top:1040px;height:56px"></div>
  <p class="abs contact-email">solvestudy@lakemont.edu</p>
  <div class="abs contact-rule"></div>

  <footer>
    <div class="abs uni"><div class="uni-mark"></div><div class="uni-name">Lakemont<br>University</div></div>
    <div class="abs band-divider" style="left:270px;top:1130px;height:56px"></div>
    <svg class="abs" style="left:291px;top:1132px" width="42" height="46" viewBox="0 0 42 46" fill="none" stroke="#3a4cb0" stroke-width="1.6" aria-hidden="true"><path d="M21 2l18 7v13c0 11-8 19-18 22C11 41 3 33 3 22V9z"/><path d="M13 23l6 6 10-11"/></svg>
    <p class="abs footer-note" style="left:347px;top:1134px">This study is conducted by<br>researchers at Lakemont<br>University.<br>All information is kept confidential.</p>
    <div class="abs band-divider" style="left:536px;top:1130px;height:56px"></div>
    <svg class="abs" style="left:556px;top:1128px" width="56" height="56" viewBox="0 0 56 56" fill="none" stroke="#a47fe2" stroke-width="1.6" aria-hidden="true"><circle cx="28" cy="28" r="27"/><rect x="19" y="26" width="18" height="14" rx="1.5"/><path d="M22 26v-4a6 6 0 0 1 12 0v4"/><path d="M28 31v4"/></svg>
    <p class="abs footer-note" style="left:627px;top:1133px;font-size:11px;line-height:16px">Your child's safety<br>and comfort are<br>our top priority.</p>
  </footer>
</main>
</body>
</html>
```